Web Design Project

I want customers to be able to book appointments to get their makeup done and make a deposit and also have a gallery where i put my portfolio images, i want it to be very simple yet elegant.

Target Market(s)

Women ranging from 18-40 that want to get their makeup done

Industry/Entity Type

Makeup

Font styles to use
Sans Serif
Decorative

Requirements
Nice to have
• easy scheduling option and option to pay service in full on website.

```html
<!DOCTYPE html>
<html lang="en">
<head>
<meta charset="utf-8">
<title>Makeup Studio — Home</title>
<link rel="stylesheet" href="https://fonts.googleapis.com/css2?family=Roboto+Condensed:wght@400;700&family=Roboto:wght@400;700&display=swap">
<style>
:root{
  --pink:#f7128a;
  --pink-deep:#d10a72;
  --ink:#2f2f2f;
  --topbar:#333333;
  --body-text:#555555;
  --espresso:#3d3431;
  --espresso-dark:#2e2725;
  --panel:#383332;
  --footer:#2b2624;
  --white:#ffffff;
}
*{box-sizing:border-box;margin:0;padding:0}
html,body{width:1200px;height:3088px;overflow:hidden}
body{font-family:"Roboto",Arial,sans-serif;color:var(--ink);background:var(--white);position:relative}
.head{font-family:"Roboto Condensed","Arial Narrow",sans-serif;font-weight:700;text-transform:uppercase}

/* top bar */
.topbar{height:52px;background:var(--topbar);color:#ddd;font-size:15px;display:flex;align-items:center;padding-left:95px;position:relative}
.topbar__search{position:absolute;right:0;top:0;width:183px;height:52px;background:var(--pink);display:flex;align-items:center;justify-content:center}

/* header */
.site-header{height:118px;display:flex;align-items:center;padding:0 95px;justify-content:space-between}
.logo{font-family:"Roboto Condensed",sans-serif;font-weight:700;font-size:48px;color:var(--pink);letter-spacing:-0.5px}
.nav{display:flex;gap:30px;font-family:"Roboto Condensed",sans-serif;font-weight:700;font-size:15px;text-transform:uppercase;color:#333}
.nav a{color:inherit;text-decoration:none}
.nav a.is-active{color:var(--pink)}

/* hero */
.hero{height:443px;position:relative;background:linear-gradient(90deg,#a88774 0%,#d9c3b8 22%,#e6dbd8 45%,#d6ccce 75%,#c9bec2 100%)}
.hero__tag{position:absolute;background:var(--pink);color:var(--white);display:flex;align-items:center;justify-content:center;white-space:nowrap;line-height:1}
.hero__tag--small{left:706px;top:118px;width:229px;height:54px;font-size:38px}
.hero__tag--large{left:610px;top:183px;width:495px;height:77px;font-size:48px}
.trap-btn{position:absolute;display:flex;align-items:center;justify-content:center;color:var(--white);font-family:"Roboto Condensed",sans-serif;font-weight:700;font-size:26px;text-transform:uppercase;white-space:nowrap}
.trap-btn svg{position:absolute;inset:0}
.trap-btn span{position:relative}
.hero .trap-btn{left:752px;top:268px;width:211px;height:54px}

/* section titles */
.box-title{position:absolute;left:50%;transform:translateX(-50%);height:54px;border:2px solid currentColor;display:flex;align-items:center;justify-content:center;font-size:25px;white-space:nowrap}

/* portfolio */
.portfolio{height:919px;position:relative}
.portfolio .box-title{top:69px;width:226px;color:#333}
.portfolio__intro{position:absolute;left:134px;width:935px;top:167px;text-align:center;font-size:13px;line-height:22px;color:var(--body-text)}
.portfolio__img{position:absolute;top:275px;height:387px;width:287px}
.portfolio .trap-btn{left:494px;top:759px;width:212px;height:52px}

/* features */
.features{height:636px;position:relative;background:radial-gradient(circle at 20% 30%,#4a3f3b 0,transparent 40%),radial-gradient(circle at 80% 70%,#4a3f3b 0,transparent 40%),var(--espresso);color:var(--white)}
.features .box-title{top:83px;width:325px;color:#ddd}
.feature{position:absolute;width:300px}
.feature__num{position:absolute;left:0;top:0;width:46px;height:46px;background:#eee;color:#333;font-family:"Roboto Condensed",sans-serif;font-weight:700;font-size:34px;display:flex;align-items:center;justify-content:center}
.feature__title{position:absolute;left:65px;top:10px;font-size:21px;white-space:nowrap}
.feature__title::after{content:"";position:absolute;left:0;top:34px;width:44px;height:3px;background:#fff}
.feature__text{position:absolute;left:0;top:64px;width:300px;font-size:13px;line-height:20px;color:#e6e0dd}
.feature__more{position:absolute;left:0;top:142px;font-family:"Roboto Condensed",sans-serif;font-weight:700;font-size:15px}

/* testimonials */
.testimonials{height:469px;position:relative}
.testimonials .box-title{top:70px;width:260px;color:#333}
.testimonial__photo{position:absolute;left:95px;top:188px;width:286px;height:219px;background:linear-gradient(135deg,#d8b89a,#a57c5a 60%,#e2d2c4)}
.testimonial__name{position:absolute;left:425px;top:220px;font-size:20px;color:#333}
.testimonial__name::after{content:"";position:absolute;left:0;top:30px;width:78px;height:3px;background:var(--pink)}
.testimonial__text{position:absolute;left:425px;top:273px;width:520px;font-size:13px;line-height:20px;color:var(--body-text)}
.testimonial__arrows{position:absolute;left:1007px;top:188px;display:flex;gap:4px}
.testimonial__arrows span{width:47px;height:44px;background:#ddd;display:flex;align-items:center;justify-content:center}

/* action panels */
.actions{height:358px;position:relative;background:radial-gradient(circle at 10% 50%,#3e3532 0,transparent 35%),var(--espresso-dark)}
.action{position:absolute;top:0;height:317px;background:var(--panel);color:#ddd;text-align:center}
.action__head{height:98px;background:var(--pink);color:var(--white);display:flex;align-items:center;justify-content:center;font-size:27px;white-space:nowrap}
.action--mid .action__head{background:var(--pink-deep)}
.action__rule{width:46px;height:2px;background:#ddd;margin:26px auto 20px}
.action__text{font-size:13px;line-height:21px;padding:0 26px}
.action__btn{display:inline-block;margin-top:22px;width:135px;height:38px;border:2px solid #ddd;font-family:"Roboto Condensed",sans-serif;font-weight:700;font-size:15px;line-height:34px;color:#eee}
.newsletter{display:flex;justify-content:center;margin:20px 0 16px}
.newsletter__field{width:185px;height:38px;background:#fff}
.newsletter__send{width:80px;height:38px;background:#ddd;border:2px solid #aaa;color:#333;font-family:"Roboto Condensed",sans-serif;font-weight:700;font-size:15px;line-height:34px}

/* footer */
.site-footer{height:93px;background:var(--footer);color:#ddd;font-size:13px;display:flex;align-items:center;padding:0 95px;position:relative}
.site-footer strong{color:#fff}
.footer-links{position:absolute;left:449px;display:flex;gap:18px;text-transform:uppercase}
.social{position:absolute;left:920px;display:flex;gap:15px}
.social span{width:26px;height:26px;border-radius:3px}
</style>
</head>
<body>

<div class="topbar">Welcome to our site visitors
  <div class="topbar__search">
    <svg width="18" height="18" viewBox="0 0 18 18"><circle cx="7.5" cy="7.5" r="5" fill="none" stroke="#fff" stroke-width="2"/><line x1="11" y1="11" x2="16" y2="16" stroke="#fff" stroke-width="2.4"/></svg>
  </div>
</div>

<header class="site-header">
  <div class="logo">YOURLOGO</div>
  <nav class="nav">
    <a class="is-active" href="#">Home</a><a href="#">About me</a><a href="#">My services</a><a href="#">Blog</a><a href="#">FAQs</a><a href="#">Contact</a>
  </nav>
</header>

<section class="hero" role="img" aria-label="Portrait of a woman with soft glam makeup">
  <div class="hero__tag hero__tag--small head">Doloremque</div>
  <div class="hero__tag hero__tag--large head">Iam aut aspernatur</div>
  <a class="trap-btn"><svg viewBox="0 0 211 54" preserveAspectRatio="none"><polygon points="0,0 211,0 193,54 18,54" fill="var(--pink)"/></svg><span>Read more</span></a>
</section>

<section class="portfolio">
  <h2 class="box-title head">My portfolio</h2>
  <p class="portfolio__intro">Lorem ipsum dolor sit amet rem eos illo omnis aut aperiam ab ipsam ipsa odit aut aperiam aut aspernatur veritatis unde sed enim accusantium laudantium sunt perspiciatis ipsam sed doloremque ipsam dolores totam unde aut illo aut veritatis explicabo dicta quia dicta veritatis dicta sunt quasi eaque rem</p>
  <div class="portfolio__img" style="left:126px;background:linear-gradient(160deg,#8a6a55,#c9a48c 55%,#e5cfc0)" role="img" aria-label="Portfolio photo: bridal makeup look"></div>
  <div class="portfolio__img" style="left:457px;background:linear-gradient(160deg,#d8cbbd,#a88c74 55%,#7d6552)" role="img" aria-label="Portfolio photo: natural makeup with knit scarf"></div>
  <div class="portfolio__img" style="left:788px;background:linear-gradient(160deg,#e2d8cf,#b88a6a 50%,#d6c3b4)" role="img" aria-label="Portfolio photo: editorial makeup with curled hair"></div>
  <a class="trap-btn"><svg viewBox="0 0 212 52" preserveAspectRatio="none"><polygon points="18,0 212,0 194,52 0,52" fill="var(--pink)"/></svg><span>View more</span></a>
</section>

<section class="features">
  <h2 class="box-title head">What you choose me</h2>
  <div class="feature" style="left:95px;top:198px"><div class="feature__num">1</div><h3 class="feature__title head">Amet voluptatem</h3><p class="feature__text">Lorem ipsum dolor sit amet rem illo omnis aperiam ab ipsam ipsa odit aut aperiam aspernatur unde enim accusantium laudantium sunt</p><span class="feature__more">READ MORE</span></div>
  <div class="feature" style="left:451px;top:198px"><div class="feature__num">2</div><h3 class="feature__title head">Amet voluptatem</h3><p class="feature__text">Lorem ipsum dolor sit amet rem illo omnis aperiam ab ipsam ipsa odit aut aperiam aspernatur unde enim accusantium laudantium sunt</p><span class="feature__more">READ MORE</span></div>
  <div class="feature" style="left:806px;top:198px"><div class="feature__num">3</div><h3 class="feature__title head">Amet voluptatem</h3><p class="feature__text">Lorem ipsum dolor sit amet rem illo omnis aperiam ab ipsam ipsa odit aut aperiam aspernatur unde enim accusantium laudantium sunt</p><span class="feature__more">READ MORE</span></div>
  <div class="feature" style="left:95px;top:407px"><div class="feature__num">4</div><h3 class="feature__title head">Amet voluptatem</h3><p class="feature__text">Lorem ipsum dolor sit amet rem illo omnis aperiam ab ipsam ipsa odit aut aperiam aspernatur unde enim accusantium laudantium sunt</p><span class="feature__more">READ MORE</span></div>
  <div class="feature" style="left:451px;top:407px"><div class="feature__num">5</div><h3 class="feature__title head">Amet voluptatem</h3><p class="feature__text">Lorem ipsum dolor sit amet rem illo omnis aperiam ab ipsam ipsa odit aut aperiam aspernatur unde enim accusantium laudantium sunt</p><span class="feature__more">READ MORE</span></div>
  <div class="feature" style="left:806px;top:407px"><div class="feature__num">6</div><h3 class="feature__title head">Amet voluptatem</h3><p class="feature__text">Lorem ipsum dolor sit amet rem illo omnis aperiam ab ipsam ipsa odit aut aperiam aspernatur unde enim accusantium laudantium sunt</p><span class="feature__more">READ MORE</span></div>
</section>

<section class="testimonials">
  <h2 class="box-title head">What they says</h2>
  <div class="testimonial__photo" role="img" aria-label="Client portrait with long wavy hair"></div>
  <h3 class="testimonial__name head">Maya Doe, 25 yo</h3>
  <p class="testimonial__text">Lorem ipsum dolor sit amet rem eos illo omnis aut aperiam ab ipsam ipsa odit aperiam aut aspernatur veritatis unde sed, sed enim accusantium laudantium sunt perspiciatis ipsam sed doloremque ....</p>
  <div class="testimonial__arrows">
    <span><svg width="16" height="24" viewBox="0 0 16 24"><polyline points="12,3 4,12 12,21" fill="none" stroke="#fff" stroke-width="3"/></svg></span>
    <span><svg width="16" height="24" viewBox="0 0 16 24"><polyline points="4,3 12,12 4,21" fill="none" stroke="#fff" stroke-width="3"/></svg></span>
  </div>
</section>

<section class="actions">
  <div class="action" style="left:95px;width:335px">
    <h3 class="action__head head">Make a deposit</h3>
    <div class="action__rule"></div>
    <p class="action__text">Lorem ipsum dolor sit amet omnis aperiam ab ipsam ipsa odit aut aperiam aspernatur veritatis unde enim accusantium laudantium</p>
    <span class="action__btn">READ MORE</span>
  </div>
  <div class="action action--mid" style="left:430px;width:337px">
    <h3 class="action__head head">Book appointments</h3>
    <div class="action__rule"></div>
    <p class="action__text">Lorem ipsum dolor sit amet omnis aperiam ab ipsam ipsa odit aut aperiam aspernatur veritatis unde enim accusantium laudantium</p>
    <span class="action__btn">READ MORE</span>
  </div>
  <div class="action" style="left:767px;width:338px">
    <h3 class="action__head head">Newsletter</h3>
    <div class="action__rule"></div>
    <p class="action__text">Lorem ipsum dolor sit amet omnis aperiam</p>
    <div class="newsletter"><div class="newsletter__field"></div><div class="newsletter__send">SEND</div></div>
    <p class="action__text">ab ipsam ipsa odit aut aperiam aspernatur veritatis unde enim accusantium laudantium</p>
  </div>
</section>

<footer class="site-footer">
  <span>© 2014 <strong>YOUR COMPANY</strong>. ALL RIGHTS RESERVED.</span>
  <div class="footer-links"><span>About us</span><span>Term and use</span><span>Privacy policy</span><span>FAQs</span><span>Contact us</span></div>
  <div class="social">
    <span style="background:#3b5998"></span><span style="background:#1da1f2"></span><span style="background:#d9261c"></span><span style="background:#0e76a8"></span><span style="background:#cb2027"></span>
  </div>
</footer>

</body>
</html>
```